Buchcover-Design für Fragenbuch
Ganz herzlichen Dank. Die Zusammenarbeit war völlig reibungslos und entspannt. Änderungswünsche wurden professionell umgesetzt und die kreativen Vorschläge fand ich super. Ich bin total glücklich mit dem Ergebnis.
Zielgruppe
Autorin und Workshopleiterin. Zielgruppe: Frauen ab 30
Aufgabenstellung
Ich benötige ein komplettes Buchcover, sowie 12 farbige Innenseiten. Es geht um ein Fragenbuch zum Ausfüllen mit dem Titel:
„Umarme deine stille Seele
Das Arbeitsheft zum Eintragen für neue seelische Balance“
Das Format des Buches beträgt 17x22cm. Es ist in 12 Wochen unterteilt. Darum hätte ich gerne zwischen den einzelnen Wochen eine farbige Seite (1. Woche, 2. Woche etc.), die designmäßig mit dem Außencover korrespondiert.
Die Farben sollten eher zart oder gedeckt sein. Auf keinen Fall jedoch kitschig. Wichtig ist mir, dass keine bestimmte Person zu sehen ist. (Foto)
Das ist meine Website www.umarme-deine-stille-seele.de

```html
<!DOCTYPE html>
<html lang="de">
<head>
<meta charset="utf-8">
<title>Umarme deine stille Seele – Cover und Wochenseite</title>
<link rel="stylesheet" href="https://fonts.googleapis.com/css2?family=Jost:wght@300;400&family=Allura&family=Libre+Baskerville&display=swap">
<style>
  :root {
    --canvas: #ffffff;
    --rose: #a8595a;
    --rose-deep: #845052;
    --line: #f3cfc5;
    --cream: #f7e0d2;
    --blush: #f4c8bc;
    --ink: #3a1f1f;
    --photo-light: #e9e7e4;
    --photo-dark: #4a4646;
  }
  * { margin: 0; padding: 0; box-sizing: border-box; }
  html, body { width: 1200px; height: 849px; overflow: hidden; background: var(--canvas); }
  .canvas { position: relative; width: 1200px; height: 849px; }

  .page { position: absolute; background: var(--rose); overflow: hidden; }
  .page svg.frame { position: absolute; inset: 0; }

  /* Cover */
  .cover { left: 233px; top: 184px; width: 362px; height: 468px; }
  .cover .title {
    position: absolute; left: 0; width: 100%; top: 57px;
    text-align: center; font-family: "Jost", sans-serif; font-weight: 300;
    font-size: 33px; line-height: 31px; color: var(--cream); letter-spacing: 0.5px;
  }
  .cover .subtitle {
    position: absolute; left: 0; width: 100%; top: 190px;
    text-align: center; font-family: "Jost", sans-serif; font-weight: 300;
    font-size: 18px; color: var(--ink); letter-spacing: 0.3px;
  }
  .cover .tagline {
    position: absolute; left: 0; width: 100%; top: 224px;
    text-align: center; font-family: "Jost", sans-serif; font-weight: 300;
    font-size: 7.5px; line-height: 11px; color: var(--ink);
  }
  .cover .author {
    position: absolute; left: 0; width: 100%; top: 322px;
    text-align: center; font-family: "Allura", cursive;
    font-size: 24px; color: var(--blush);
  }
  .cover .services {
    position: absolute; left: 0; width: 100%; top: 379px;
    text-align: center; font-family: "Libre Baskerville", serif;
    font-size: 6.5px; line-height: 11.6px; color: var(--blush);
  }

  /* Week divider */
  .week { left: 660px; top: 182px; width: 365px; height: 471px; }
  .week .number {
    position: absolute; left: 58px; top: 10px;
    font-family: "Jost", sans-serif; font-weight: 300;
    font-size: 160px; line-height: 160px; color: var(--cream);
  }
  .week .label {
    position: absolute; left: 60px; top: 148px;
    font-family: "Jost", sans-serif; font-weight: 300;
    font-size: 60px; line-height: 70px; color: var(--cream);
  }
  .week .heading {
    position: absolute; left: 63px; top: 218px;
    font-family: "Jost", sans-serif; font-weight: 300;
    font-size: 34px; line-height: 40px; color: var(--ink);
  }
  .week .heading-rule {
    position: absolute; left: 64px; top: 261px; width: 156px; height: 1px; background: var(--line);
  }
  .week .ghost-number {
    position: absolute; right: 38px; top: 300px;
    font-family: "Jost", sans-serif; font-weight: 300;
    font-size: 160px; line-height: 160px; color: var(--cream); opacity: 0.35;
  }
</style>
</head>
<body>
<main class="canvas">

  <section class="page cover" aria-label="Buchcover">
    <svg class="frame" width="362" height="468" viewBox="0 0 362 468">
      <g fill="none" stroke="var(--line)" stroke-width="1.2">
        <line x1="36" y1="0" x2="36" y2="468"/>
        <line x1="326" y1="0" x2="326" y2="468"/>
        <line x1="0" y1="21" x2="362" y2="21"/>
        <line x1="0" y1="443" x2="362" y2="443"/>
        <path d="M37 443 V418 A144 144 0 0 1 325 418 V443"/>
      </g>
    </svg>
    <h1 class="title">UMARME<br>DEINE<br>STILLE<br>SEELE</h1>
    <p class="subtitle">DAS ARBEITSHEFT</p>
    <p class="tagline">ZUM EINTRAGEN<br>FÜR NEUE SEELISCHE BALANCE</p>
    <p class="author">by Mara Lindholm</p>
    <p class="services">COACHING<br>•<br>MENTORING<br>•<br>2021</p>
  </section>

  <section class="page week" aria-label="Wochenseite">
    <svg class="frame" width="365" height="471" viewBox="0 0 365 471">
      <defs>
        <linearGradient id="photoTone" x1="0" y1="0" x2="1" y2="1">
          <stop offset="0" stop-color="var(--photo-dark)"/>
          <stop offset="0.35" stop-color="var(--photo-light)"/>
          <stop offset="1" stop-color="#d9d6d2"/>
        </linearGradient>
      </defs>
      <g fill="none" stroke="var(--line)" stroke-width="1.2">
        <line x1="41" y1="0" x2="41" y2="471"/>
        <line x1="333" y1="0" x2="333" y2="471"/>
        <line x1="0" y1="23" x2="365" y2="23"/>
      </g>
      <path d="M41 471 V409 A95 95 0 0 1 231 409 V471 Z" fill="var(--rose-deep)"/>
      <path d="M70 471 V404 A63.5 63.5 0 0 1 197 404 V471 Z" fill="url(#photoTone)"
            role="img" aria-label="Foto: Oberkörper in hellem Strickpullover mit Kettenanhänger"/>
    </svg>
    <div class="number">3</div>
    <div class="label">WOCHE</div>
    <div class="heading">TITLE HERE</div>
    <div class="heading-rule"></div>
    <div class="ghost-number">3</div>
  </section>

</main>
</body>
</html>
```